Website for Reiki and Wellness Courses

I teach online courses in Reiki and wellness/self-development and am needing a new website.

The focus of the website will be to provide descriptions of the courses as well as include a blog and pages where students in my courses will visit for additional information.

Note: courses are NOT hosted on this site.
The focus of this website will be to encourage viewers to enroll in courses as well as opt in to the email list.

I will upload copy soon. My old website is: http://brightfernstudies.example. Please do not use existing logo.

Target Market(s)

Alternative health, wellness, spirituality, personal development. Males and females of all ages seeking to improve their health and life.

Industry/Entity Type

Health And Wellness

Logo Text

No text (please do not use existing logo)

Coding

Coded - Design and coding required

Number of Pages Required

5+ page

Requirements
Must have
• 1. Home page
• 2. About page
• 3. Courses page that outlines courses (there are currently 6 courses with 1 coming soon)
• 4. Individual course page (maybe a template that I can adjust color and pictures for with each course)
• 5. Blog
• 6. Student Area that outlines all Student Areas
• 7. Individual Student Area page (maybe a template that I can adjust color and pictures for with each course)
• 8. Shop page (note: items will not currently be purchased through website - it will be a link to quillmarket for a book).
• 9. Student thank-you page (maybe a template that I can adjust color and pictures for with each course) this is the page students are directed to at end of course with vouchers for other courses.
• Opt-in for the home page, course pages, blog and thank-you pages
Nice to have
• I would like the design to be calm, clean and soothing. Ideally visitors feel relaxed when viewing the site and are encouraged to explore the courses, subscribe to the email list and purchase a product.
• ~ Testimonials page
• ~ Contact page
• I tend to gravitate towards blues, greys and purples as well as monochromatic color schemes.
Should not have
• Contact form on home page
• phone number on home page
• location/physical address
• dates for blog posts

```html
<!DOCTYPE html>
<html lang="en">
<head>
<meta charset="utf-8">
<title>Bright Fern Studies — Become a Certified Usui Reiki Master</title>
<link href="https://fonts.googleapis.com/css2?family=Montserrat:wght@300;400;500;600&family=Open+Sans:wght@400;600&family=Great+Vibes&display=swap" rel="stylesheet">
<style>
:root{
  --coral:#e47a61;
  --coral-soft:#ea9d8b;
  --ink:#2f2f2f;
  --muted:#7a7a7a;
  --line:#e3e3e3;
  --panel:#f3f3f3;
  --white:#ffffff;
  --dusk-top:#7f8a96;
  --dusk-mid:#c9a98a;
  --dusk-glow:#f0c98e;
  --dusk-hill:#5d6b74;
  --robe-grey:#a8a3a6;
  --robe-purple:#5a3f66;
}
*{margin:0;padding:0;box-sizing:border-box}
html,body{width:1200px;height:3600px;overflow:hidden;background:var(--white)}
body{position:relative;font-family:"Open Sans",Arial,sans-serif;color:var(--ink)}
.abs{position:absolute}
.script{font-family:"Great Vibes",cursive;color:var(--coral);font-size:36px;text-align:center;width:100%}
.section-title{font-family:"Montserrat",Arial,sans-serif;font-weight:300;font-size:38px;letter-spacing:1px;text-align:center;width:100%;text-transform:uppercase}

/* hero */
.hero{top:0;left:0;width:1200px;height:600px}
.brand{top:22px;left:80px;display:flex;align-items:center;gap:14px;color:var(--white);font-family:"Montserrat",sans-serif;font-weight:500;font-size:24px}
.brand-mark{width:42px;height:42px;background:var(--coral);transform:rotate(45deg)}
.nav{top:42px;right:80px;display:flex;gap:42px;font-family:"Montserrat",sans-serif;font-size:15px;color:var(--white);text-transform:uppercase;letter-spacing:.5px}
.nav .active{color:var(--coral)}
.hero-figure{top:150px;left:575px;width:500px;height:520px;border-radius:250px 250px 60px 60px;background:linear-gradient(180deg,rgba(168,163,166,.85) 0%,var(--robe-grey) 40%,#8a7c8c 62%,var(--robe-purple) 100%)}
.hero-title{top:160px;left:80px;width:620px;font-family:"Montserrat",sans-serif;font-weight:300;font-size:50px;line-height:60px;color:var(--white);text-transform:uppercase;letter-spacing:1px}
.hero-copy{top:302px;left:80px;width:540px;font-size:23px;line-height:31px;color:var(--white)}
.watch{top:530px;left:80px;display:flex;align-items:center;gap:22px}
.watch-btn{width:66px;height:66px;border:2px solid var(--coral);border-radius:50%;display:flex;align-items:center;justify-content:center}
.watch small{display:block;font-size:14px;color:var(--ink)}
.watch strong{font-family:"Montserrat",sans-serif;font-weight:500;font-size:20px;letter-spacing:1px;border-bottom:2px solid var(--ink)}

/* intro quote */
.quote{top:700px;left:120px;width:960px;text-align:center;font-size:22px;line-height:33px;color:var(--ink)}
.quote-author{top:830px;width:1200px;text-align:center;font-family:"Montserrat",sans-serif;font-size:18px;font-weight:500}
.divider{top:906px;left:80px;width:1040px;height:1px;background:var(--line)}
.feature{top:960px;width:330px;text-align:center}
.feature-icon{width:144px;height:144px;border-radius:50%;background:#ededed;margin:0 auto 28px;display:flex;align-items:center;justify-content:center}
.feature h3{font-family:"Montserrat",sans-serif;font-weight:600;font-size:18px;margin-bottom:10px}
.feature p{font-size:14px;line-height:24px;color:var(--muted)}

/* classes */
.classes{top:1308px;left:0;width:1200px;height:559px;background:var(--panel)}
.card{top:1471px;width:250px;height:346px;background:var(--white);box-shadow:0 2px 6px rgba(0,0,0,.08);text-align:center}
.card-photo{height:125px}
.avatar{width:60px;height:60px;border-radius:50%;border:3px solid var(--white);margin:-20px auto 0;position:relative}
.teacher{margin-top:16px;font-family:"Montserrat",sans-serif;font-size:13px;text-transform:uppercase}
.course{margin-top:12px;font-family:"Montserrat",sans-serif;font-size:18px}
.stats{position:absolute;left:0;bottom:0;width:100%;height:60px;border-top:1px solid var(--line);display:flex;align-items:center;justify-content:space-around;font-size:13px;color:var(--muted)}
.stats span{display:flex;align-items:center;gap:6px}
.stats .price{color:var(--coral);font-weight:600;font-size:15px}
.view-more{position:absolute;left:0;bottom:14px;width:100%;height:46px;background:var(--coral);color:var(--white);font-family:"Montserrat",sans-serif;font-size:14px;letter-spacing:1px;display:flex;align-items:center;justify-content:center;gap:10px}

/* testimonials */
.testimonials{top:1867px;left:0;width:1200px;height:461px;background:linear-gradient(180deg,#4c4640 0%,#6c5f52 45%,#3a332e 100%)}
.testimonial-avatar{top:2026px;left:557px;width:86px;height:86px;border-radius:50%;border:3px solid var(--white);background:#b7c4c9}
.testimonial-body{top:2132px;left:210px;width:780px;display:flex;flex-direction:column;align-items:center;text-align:center;color:var(--white)}
.testimonial-text{font-size:13.5px;line-height:24px}
.stars{margin-top:6px;color:#f1c23c;font-size:18px;line-height:22px;letter-spacing:2px}
.client{margin-top:14px;font-family:"Montserrat",sans-serif;font-size:15px}
.client b{color:var(--coral);font-weight:500;letter-spacing:1px}

/* store */
.store{top:2328px;left:0;width:1200px;height:247px;background:var(--coral)}
.store-title{top:2418px;left:80px;font-family:"Montserrat",sans-serif;font-weight:300;font-size:38px;color:var(--white);text-transform:uppercase;letter-spacing:1px}
.btn-light{top:2474px;left:79px;width:163px;height:50px;border-radius:25px;background:var(--white);color:var(--coral);font-family:"Montserrat",sans-serif;font-weight:600;font-size:15px;display:flex;align-items:center;justify-content:center;letter-spacing:1px}
.book{box-shadow:6px 8px 16px rgba(0,0,0,.3)}

/* blog */
.post{top:2731px;width:331px;height:382px;background:var(--white);box-shadow:0 2px 6px rgba(0,0,0,.08);text-align:center}
.post-photo{height:190px}
.post-cat{margin-top:22px;font-size:13px;color:var(--muted);text-transform:uppercase;letter-spacing:.5px}
.post h4{margin-top:8px;font-family:"Montserrat",sans-serif;font-weight:500;font-size:18px}
.post p{margin:12px 40px 0;font-size:14px;line-height:22px;color:var(--muted)}
.post-meta{position:absolute;bottom:0;left:0;width:100%;height:56px;border-top:1px solid var(--line);display:flex;align-items:center;justify-content:space-around;font-size:13px;color:var(--muted)}
.post-meta span{display:flex;align-items:center;gap:6px}

/* newsletter */
.newsletter{top:3163px;left:0;width:1200px;height:317px;background:radial-gradient(ellipse at 50% 45%,#f6cfc4 0%,var(--coral-soft) 55%,#e4907c 100%)}
.news-mark{top:3226px;left:582px;width:36px;height:36px;border:2px solid var(--white);transform:rotate(45deg)}
.news-title{top:3304px;width:1200px;text-align:center;font-family:"Montserrat",sans-serif;font-weight:300;font-size:36px;color:var(--ink);letter-spacing:1.5px}
.field{top:3382px;width:330px;border-bottom:1px solid var(--white);padding-bottom:10px;font-size:14px;color:var(--ink)}
.btn-submit{top:3374px;left:874px;width:144px;height:50px;border-radius:25px;background:var(--white);color:var(--coral);font-family:"Montserrat",sans-serif;font-weight:600;font-size:15px;display:flex;align-items:center;justify-content:center;letter-spacing:1px}

/* footer */
.footer{top:3480px;left:0;width:1200px;height:120px;background:var(--white)}
.footer-brand{top:3514px;left:80px;display:flex;align-items:center;gap:14px;font-family:"Montserrat",sans-serif;font-size:19px;color:var(--coral)}
.footer-brand .brand-mark{width:32px;height:32px}
.copyright{top:3528px;left:400px;font-family:"Montserrat",sans-serif;font-size:13px;color:var(--ink)}
.copyright b{color:var(--coral);font-weight:500}
.social{top:3512px;left:884px;display:flex;gap:24px}
.social i{display:block;width:40px;height:40px;border:1.5px solid #cfcfcf;transform:rotate(45deg)}
.social i.on{background:var(--coral);border-color:var(--coral)}
.footer-bar{top:3588px;left:0;width:1200px;height:12px;background:var(--coral)}
</style>
</head>
<body>

<!-- HERO -->
<svg class="abs hero" viewBox="0 0 1200 600" role="img" aria-label="Photo of misty mountain ranges at sunset with a warm glowing sky">
  <defs>
    <linearGradient id="sky" x1="0" y1="0" x2="0" y2="1">
      <stop offset="0" stop-color="var(--dusk-top)"/>
      <stop offset=".45" stop-color="var(--dusk-mid)"/>
      <stop offset=".62" stop-color="var(--dusk-glow)"/>
      <stop offset="1" stop-color="var(--dusk-hill)"/>
    </linearGradient>
  </defs>
  <polygon points="0,0 1200,0 1200,600 0,490" fill="url(#sky)"/>
</svg>

<div class="abs brand"><span class="brand-mark"></span>Bright Fern Studies</div>
<nav class="abs nav">
  <span class="active">Home</span><span>About</span><span>Courses</span><span>Blog</span><span>Student Areas</span><span>Contact</span>
</nav>

<div class="abs hero-figure" role="img" aria-label="Photo of a woman meditating in lotus position, wearing a grey top and purple trousers"></div>

<h1 class="abs hero-title">Become a Certified Usui Reiki Master</h1>
<p class="abs hero-copy">This Comprehensive online course gives you all of the tools you need to be certified as a Traditional Usui Reiki Master.</p>

<div class="abs watch">
  <div class="watch-btn"><svg width="22" height="24" viewBox="0 0 22 24"><polygon points="3,2 20,12 3,22" fill="none" stroke="var(--coral)" stroke-width="2"/></svg></div>
  <div><small>Watch</small><strong>INTRO VIDEO</strong></div>
</div>

<!-- INTRO -->
<p class="abs quote">Have you ever seen a mother kiss a child's elbow after they fall? What is your response when you stub your toe or bang your shin? We instinctively touch and focus on areas in pain or need. Reiki is an extension of this innate wisdom.</p>
<p class="abs quote-author">- LENA MARSH</p>
<div class="abs divider"></div>

<div class="abs feature" style="left:75px">
  <div class="feature-icon">
    <svg width="64" height="64" viewBox="0 0 64 64" fill="none" stroke="var(--coral)" stroke-width="2" stroke-linecap="round">
      <path d="M10 14 C12 30 16 42 26 50 L28 58"/><path d="M54 14 C52 30 48 42 38 50 L36 58"/>
      <path d="M16 22 L18 36"/><path d="M48 22 L46 36"/><path d="M22 40 L28 46"/><path d="M42 40 L36 46"/>
    </svg>
  </div>
  <h3>How Reiki Works</h3>
  <p>Reiki has been used for centuries to help individuals with physical and emotional imbalances as well as those seeking clarity and enlightenment.</p>
</div>
<div class="abs feature" style="left:435px">
  <div class="feature-icon">
    <svg width="64" height="64" viewBox="0 0 64 64" fill="none" stroke="var(--coral)" stroke-width="2" stroke-linecap="round">
      <circle cx="32" cy="32" r="9"/>
      <path d="M32 10v8M32 46v8M10 32h8M46 32h8M16 16l6 6M42 42l6 6M48 16l-6 6M22 42l-6 6"/>
    </svg>
  </div>
  <h3>Usui Reiki Master Certification</h3>
  <p>Learn how to use Reiki to help yourself and others.</p>
</div>
<div class="abs feature" style="left:795px">
  <div class="feature-icon">
    <svg width="64" height="64" viewBox="0 0 64 64" fill="none" stroke="var(--coral)" stroke-width="2" stroke-linejoin="round">
      <path d="M32 18 C24 14 16 14 8 16 V50 C16 48 24 48 32 52 C40 48 48 48 56 50 V16 C48 14 40 14 32 18 Z"/>
      <path d="M32 18 V52"/><path d="M14 24h12M14 30h12M14 36h12M38 24h12M38 30h12M38 36h12"/>
    </svg>
  </div>
  <h3>Resources</h3>
  <p>Information and tools to help you create a life you love.</p>
</div>

<!-- CLASSES -->
<section class="abs classes"></section>
<p class="abs script" style="top:1352px">Choose your level &amp; focus</p>
<h2 class="abs section-title" style="top:1396px">Discover Our Classes</h2>

<article class="abs card" style="left:79px">
  <div class="card-photo" role="img" aria-label="Photo of stacked pebbles on a beach with turquoise sea" style="background:linear-gradient(180deg,#7fb7d6 0%,#3f9bbd 55%,#e7e4dc 100%)"></div>
  <div class="avatar" role="img" aria-label="Teacher portrait" style="background:#8fb0b8"></div>
  <p class="teacher">Lena Marsh</p>
  <p class="course">Reiki Certification</p>
  <div class="stats"><span><svg width="14" height="14" viewBox="0 0 14 14"><circle cx="7" cy="4" r="3" fill="#999"/><path d="M1 14c0-4 3-6 6-6s6 2 6 6z" fill="#999"/></svg>27,033</span><span><svg width="14" height="14" viewBox="0 0 14 14"><path d="M1 6h3v8H1zM5 14V6l3-5c2 0 2 2 1 4h4l-1 9z" fill="#999"/></svg>4.7</span><span class="price">$195</span></div>
</article>
<article class="abs card" style="left:343px">
  <div class="card-photo" role="img" aria-label="Photo of hands resting on a small white dog" style="background:linear-gradient(180deg,#9fb6d1 0%,#e9e3da 60%,#cdbfae 100%)"></div>
  <div class="avatar" role="img" aria-label="Teacher portrait" style="background:#8fb0b8"></div>
  <p class="teacher">Lena Marsh</p>
  <p class="course">Animal Reiki Certification</p>
  <div class="stats"><span><svg width="14" height="14" viewBox="0 0 14 14"><circle cx="7" cy="4" r="3" fill="#999"/><path d="M1 14c0-4 3-6 6-6s6 2 6 6z" fill="#999"/></svg>2,431</span><span><svg width="14" height="14" viewBox="0 0 14 14"><path d="M1 6h3v8H1zM5 14V6l3-5c2 0 2 2 1 4h4l-1 9z" fill="#999"/></svg>4.7</span><span class="price">$50</span></div>
</article>
<article class="abs card" style="left:607px">
  <div class="card-photo" role="img" aria-label="Photo of a relaxed person receiving acupressure on the face" style="background:linear-gradient(180deg,#e9d6c8 0%,#d9b49c 60%,#f2ece6 100%)"></div>
  <div class="avatar" role="img" aria-label="Teacher portrait" style="background:#a9b7bd"></div>
  <p class="teacher">Dr. Tomas Veller</p>
  <p class="course">Acupressure &amp; Reiki</p>
  <div class="view-more">VIEW MORE <svg width="16" height="12" viewBox="0 0 16 12"><path d="M0 6h14M9 1l5 5-5 5" fill="none" stroke="#fff" stroke-width="1.6"/></svg></div>
</article>
<article class="abs card" style="left:871px">
  <div class="card-photo" role="img" aria-label="Photo of a person with raised arms at a lake at sunrise" style="background:linear-gradient(180deg,#c9c39a 0%,#9ea26a 55%,#4f5a3a 100%)"></div>
  <div class="avatar" role="img" aria-label="Teacher portrait" style="background:#8fb0b8"></div>
  <p class="teacher">Lena Marsh</p>
  <p class="course">Our Soul is Calling</p>
  <div class="stats"><span><svg width="14" height="14" viewBox="0 0 14 14"><circle cx="7" cy="4" r="3" fill="#999"/><path d="M1 14c0-4 3-6 6-6s6 2 6 6z" fill="#999"/></svg>2,251</span><span><svg width="14" height="14" viewBox="0 0 14 14"><path d="M1 6h3v8H1zM5 14V6l3-5c2 0 2 2 1 4h4l-1 9z" fill="#999"/></svg>4.6</span><span class="price">$45</span></div>
</article>

<!-- TESTIMONIALS -->
<section class="abs testimonials" role="img" aria-label="Photo of a person with raised arms on a rocky shore beside stacked stones at dusk"></section>
<p class="abs script" style="top:1910px">Testimonials</p>
<h2 class="abs section-title" style="top:1958px;color:var(--white)">Happy Clients</h2>
<div class="abs testimonial-avatar" role="img" aria-label="Client portrait"></div>
<div class="abs testimonial-body">
  <p class="testimonial-text">I am in LOVE with this course. Not only is it packed with lots of information to guide you toward understanding and appreciating Reiki, but it's also highly inspiring and transformative! All of the lectures are really special. I love how focused they are. Every piece of information being delivered is very powerful and eye-opening!</p>
  <p class="stars">★★★★★</p>
  <p class="client"><b>RUTH DALMAN</b> &nbsp;/&nbsp; Reiki level 2</p>
</div>

<!-- STORE -->
<section class="abs store"></section>
<p class="abs script" style="top:2372px;left:80px;width:auto;color:var(--white);text-align:left">Welcome to the Store</p>
<h2 class="abs store-title">Check Out Our Products</h2>
<div class="abs btn-light">SHOP NOW</div>
<div class="abs book" style="top:2300px;left:804px;width:176px;height:290px;background:linear-gradient(160deg,#3d6aa8 0%,#8a4e9c 40%,#d6a04c 75%,#f0ede6 100%)" role="img" aria-label="Book cover with a colourful painted face"></div>
<div class="abs book" style="top:2292px;left:972px;width:160px;height:280px;background:linear-gradient(180deg,#eef5f6 0%,#4fa9c7 55%,#1e4f6e 100%)" role="img" aria-label="Book cover for a Reiki Level 2 manual with a blue water spiral"></div>

<!-- BLOG -->
<p class="abs script" style="top:2620px">Latest Post</p>
<h2 class="abs section-title" style="top:2668px">From Blog</h2>

<article class="abs post" style="left:79px">
  <div class="post-photo" role="img" aria-label="Photo of a hand held above an older man's forehead during a Reiki session" style="background:linear-gradient(180deg,#cfd6dc 0%,#9eaebd 50%,#e6e2dc 100%)"></div>
  <p class="post-cat">Life Style</p>
  <h4>Ways to Get Motivated</h4>
  <p>Lorem Ipsum is simply dummy text of the printing and typesetting industry.</p>
  <div class="post-meta"><span><svg width="14" height="14" viewBox="0 0 14 14" fill="none" stroke="var(--coral)" stroke-width="1.4"><rect x="1" y="2" width="12" height="11"/><path d="M1 5h12"/></svg>Oct 1st, 2016</span><span><svg width="14" height="14" viewBox="0 0 14 14" fill="none" stroke="var(--coral)" stroke-width="1.4"><path d="M1 2h12v8H5l-3 3v-3H1z"/></svg>4</span><span><svg width="14" height="13" viewBox="0 0 14 13" fill="none" stroke="var(--coral)" stroke-width="1.4"><path d="M7 12L1.5 6.5A3 3 0 017 2.5a3 3 0 015.5 4z"/></svg>134</span></div>
</article>
<article class="abs post" style="left:434px">
  <div class="post-photo" role="img" aria-label="Photo of a woman meditating beside a waterfall and a turquoise pool" style="background:linear-gradient(180deg,#6f8e55 0%,#a4b7a0 45%,#5fb8c0 100%)"></div>
  <p class="post-cat">Meditation</p>
  <h4>Take Charge of Your Life</h4>
  <p>Lorem Ipsum is simply dummy text of the printing and typesetting industry.</p>
  <div class="post-meta"><span><svg width="14" height="14" viewBox="0 0 14 14" fill="none" stroke="var(--coral)" stroke-width="1.4"><rect x="1" y="2" width="12" height="11"/><path d="M1 5h12"/></svg>Oct 1st, 2016</span><span><svg width="14" height="14" viewBox="0 0 14 14" fill="none" stroke="var(--coral)" stroke-width="1.4"><path d="M1 2h12v8H5l-3 3v-3H1z"/></svg>4</span><span><svg width="14" height="13" viewBox="0 0 14 13" fill="none" stroke="var(--coral)" stroke-width="1.4"><path d="M7 12L1.5 6.5A3 3 0 017 2.5a3 3 0 015.5 4z"/></svg>134</span></div>
</article>
<article class="abs post" style="left:790px">
  <div class="post-photo" role="img" aria-label="Photo of a person holding a black and white cat" style="background:linear-gradient(180deg,#d8d2cb 0%,#b8aca0 55%,#e9e6e1 100%)"></div>
  <p class="post-cat">Animal Reiki</p>
  <h4>Communicate with Animals</h4>
  <p>Lorem Ipsum is simply dummy text of the printing and typesetting industry.</p>
  <div class="post-meta"><span><svg width="14" height="14" viewBox="0 0 14 14" fill="none" stroke="var(--coral)" stroke-width="1.4"><rect x="1" y="2" width="12" height="11"/><path d="M1 5h12"/></svg>Oct 1st, 2016</span><span><svg width="14" height="14" viewBox="0 0 14 14" fill="none" stroke="var(--coral)" stroke-width="1.4"><path d="M1 2h12v8H5l-3 3v-3H1z"/></svg>4</span><span><svg width="14" height="13" viewBox="0 0 14 13" fill="none" stroke="var(--coral)" stroke-width="1.4"><path d="M7 12L1.5 6.5A3 3 0 017 2.5a3 3 0 015.5 4z"/></svg>134</span></div>
</article>

<!-- NEWSLETTER -->
<section class="abs newsletter"></section>
<div class="abs news-mark"></div>
<h2 class="abs news-title">SIGN UP FOR OUR NEWSLETTER</h2>
<div class="abs field" style="left:182px">Your Name</div>
<div class="abs field" style="left:530px">Your E-Mail</div>
<div class="abs btn-submit">SUBMIT</div>

<!-- FOOTER -->
<footer class="abs footer"></footer>
<div class="abs footer-brand"><span class="brand-mark"></span>Bright Fern Studies</div>
<p class="abs copyright">© <b>BRIGHT FERN STUDIES</b> - 2016. All Rights Reserved.</p>
<div class="abs social" aria-label="Social links">
  <i class="on"></i><i></i><i></i><i></i>
</div>
<div class="abs footer-bar"></div>

</body>
</html>
```